Business Card (double-sided) and Stationary Design for dental office

1) Business Card Design: We need a business card design for a dental specialty office.
Texts should contain:
The name of our office "Brindle Oaks Orthodontics"
Tagline: "Specialist in Orthodontic and Maxillofacial Orthopedics"
Tag line: "Creating "Tolvering" smiles for Children and Adults"
Doctor name: "Doctor Name"
Office Address:
"123 Street Name
City, State Zip code"
Office email address: office@brindleoaksortho.com
Website: www.brindleoaksortho.com

We will provide the full office address once the design is selected
Theme: beach, paradise, coastal, wave
We would like to have some creativity in design. Some acceptable ideas: front page: logo and office name. Back page: more detail information, and map to office in form of an island. Please see sample from our other location, but you DON'T HAVE TO USE OR COPY THE SAME CONCEPT.

IF POSSIBLE, PLEASE SUBMIT AT LEAST TWO CONCEPTS: ONE WITH THE BACK LOOKING SIMILAR TO WHAT IS IN THE SAMPLE, AND ONE DIFFERENT.

Color: designer to choose. We have different shade of blues and sand color in our office. Please see logo.

2) Please also design a matching set of stationary that compliment the business card and our logo.

Target Market(s)

Dental

Contact Information for Business Card

See descriptions

Font styles to use
Other font styles liked:
• Matching texts in logo

Colors
0054AA
0677BA
7BADD7
CADEEF
E8F1F8
0094D4
00A9DD
6FCCEA
C7EBF8
E9F6FB
00AB8E
00BBA5
67D7C9
C6EFE9
E9F9F6

Requirements
Must have
• Double-sided
Nice to have
• Beach coastal theme
Should not have
• Any shape or drawing of of tooth or teeth. We don’t need these. You don't necessarily have to just cut and paste the logo art and text as a whole, you have the liberty to rearrange the text.

```html
<!DOCTYPE html>
<html lang="en">
<head>
<meta charset="utf-8">
<title>Brindle Oaks Orthodontics – Business Card</title>
<link href="https://fonts.googleapis.com/css2?family=Montserrat:wght@400;500;700&family=Roboto:wght@400;500&display=swap" rel="stylesheet">
<style>
  :root {
    --bg: #e6e9ec;
    --card: #ffffff;
    --card-back: #f4f4f4;
    --pattern: #ececec;
    --teal: #2f8aa8;
    --mint: #6fccbf;
    --ink: #333a40;
    --ink-soft: #555b60;
    --dots: #4a4f54;
    --box: #7a7f84;
    --divider: #c9ced2;
  }
  * { box-sizing: border-box; margin: 0; padding: 0; }
  html, body { width: 1200px; height: 1015px; overflow: hidden; }
  body {
    background: var(--bg);
    font-family: "Roboto", Arial, sans-serif;
    color: var(--ink);
    display: flex;
    flex-direction: column;
    align-items: center;
    justify-content: center;
    gap: 40px;
  }
  .card {
    position: relative;
    width: 760px;
    height: 434px;
    background: var(--card);
    box-shadow: 0 6px 20px rgba(0,0,0,.18);
    overflow: hidden;
  }

  /* ---------- appointment side ---------- */
  .card--appointment { background: var(--card-back); }
  .appointment__pattern {
    position: absolute; inset: 0;
    background: radial-gradient(circle at 50% 50%, var(--card-back) 0%, var(--pattern) 100%);
  }
  .appointment__body { position: relative; padding: 34px 60px 0; }
  .appointment__title {
    text-align: center;
    font-family: "Roboto", Arial, sans-serif;
    font-weight: 500;
    font-size: 27px;
    letter-spacing: .5px;
    color: var(--ink);
    margin-bottom: 22px;
  }
  .form-row {
    display: flex; align-items: flex-end; gap: 6px;
    font-size: 19px; color: var(--ink-soft);
    height: 40px;
  }
  .form-row .fill { flex: 1; border-bottom: 2px dotted var(--dots); margin-bottom: 6px; }
  .form-row .fill--short { flex: 0 0 230px; }
  .days { display: flex; justify-content: space-between; margin: 20px 0 10px; }
  .day { display: flex; align-items: center; gap: 8px; font-size: 20px; color: var(--ink-soft); }
  .day .box { width: 30px; height: 24px; border: 2px solid var(--box); background: #fff; }
  .appointment__notice {
    margin-top: 26px;
    text-align: center;
    font-size: 14px; line-height: 1.3;
    color: var(--ink);
  }

  /* ---------- contact side ---------- */
  .brand {
    position: absolute; left: 48px; top: 92px; width: 320px;
    text-align: center;
  }
  .brand__mark {
    width: 86px; height: 86px; border-radius: 50%;
    background: var(--teal); margin: 0 auto 18px;
  }
  .brand__name {
    font-family: "Montserrat", Arial, sans-serif;
    font-weight: 700; font-size: 30px; line-height: 1.1;
    color: var(--teal);
  }
  .brand__sub {
    margin-top: 8px;
    font-family: "Montserrat", Arial, sans-serif;
    font-weight: 500; font-size: 13px; letter-spacing: 2px;
    color: var(--mint);
  }
  .divider { position: absolute; left: 0; top: 0; }
  .contact { position: absolute; left: 432px; top: 46px; }
  .contact__name {
    font-family: "Montserrat", Arial, sans-serif;
    font-weight: 700; font-size: 31px; color: var(--teal);
  }
  .contact__role { font-family: "Montserrat", Arial, sans-serif; font-size: 18px; color: var(--ink); margin-bottom: 14px; }
  .contact__address { font-family: "Montserrat", Arial, sans-serif; font-size: 18px; line-height: 1.3; color: var(--ink); margin-bottom: 14px; }
  .contact__line { display: flex; align-items: center; gap: 8px; font-family: "Montserrat", Arial, sans-serif; font-size: 17px; color: var(--ink); line-height: 1.45; }
  .contact__line svg { flex: 0 0 18px; }
  .taglines {
    position: absolute; right: 40px; top: 318px;
    text-align: left;
    font-family: "Montserrat", Arial, sans-serif; font-weight: 500;
  }
  .taglines__primary { font-size: 22px; color: var(--teal); padding-bottom: 4px; border-bottom: 2px solid var(--mint); }
  .taglines__secondary { font-size: 21px; color: var(--mint); padding-top: 4px; padding-left: 46px; }
</style>
</head>
<body>

  <section class="card card--appointment">
    <div class="appointment__pattern" role="img" aria-label="Faint repeating practice-mark pattern in light grey"></div>
    <div class="appointment__body">
      <h2 class="appointment__title">NEXT APPOINTMENT</h2>
      <div class="form-row"><span class="fill"></span><span>has an appointment</span></div>
      <div class="form-row"><span>Date</span><span class="fill"></span><span>Time</span><span class="fill"></span><span>AM/PM</span></div>
      <div class="days">
        <label class="day"><span class="box"></span>Mon</label>
        <label class="day"><span class="box"></span>Tue</label>
        <label class="day"><span class="box"></span>Wed</label>
        <label class="day"><span class="box"></span>Thu</label>
        <label class="day"><span class="box"></span>Fri</label>
        <label class="day"><span class="box"></span>Sat</label>
      </div>
      <div class="form-row"><span>Note</span><span class="fill"></span></div>
      <div class="form-row"><span class="fill"></span></div>
      <p class="appointment__notice">Please give me 24 hours notice if you are unable to keep your<br>appointment or a cancellation fee may be charged</p>
    </div>
  </section>

  <section class="card card--contact">
    <div class="brand">
      <div class="brand__mark"></div>
      <div class="brand__name">Brindle Oaks Orthodontics</div>
      <div class="brand__sub">Pediatric Dentistry &amp; Orthodontics</div>
    </div>

    <svg class="divider" width="760" height="434" aria-hidden="true">
      <line x1="392" y1="20" x2="420" y2="290" stroke="var(--divider)" stroke-width="1.5"/>
    </svg>

    <div class="contact">
      <div class="contact__name">Harlan Mercer</div>
      <div class="contact__role">Managing Director</div>
      <div class="contact__address">123 Street Name<br>City, State Zip code</div>
      <div class="contact__line">
        <svg width="18" height="14" viewBox="0 0 18 14" aria-hidden="true"><rect width="18" height="14" rx="1" fill="var(--teal)"/><path d="M1 1l8 7 8-7" fill="none" stroke="#fff" stroke-width="1.6"/></svg>
        office@brindleoaksortho.com
      </div>
      <div class="contact__line">
        <svg width="18" height="18" viewBox="0 0 18 18" aria-hidden="true"><g fill="none" stroke="var(--teal)" stroke-width="1.5"><circle cx="9" cy="9" r="8"/><ellipse cx="9" cy="9" rx="3.5" ry="8"/><path d="M1 9h16M2.5 5h13M2.5 13h13"/></g></svg>
        www.brindleoaksortho.com
      </div>
    </div>

    <div class="taglines">
      <div class="taglines__primary">Specialist in Orthodontic and Maxillofacial Orthopedics</div>
      <div class="taglines__secondary">Creating Tolvering smiles for Children and Adults</div>
    </div>
  </section>

</body>
</html>
```